Velvette by Marisa Dunn business cards

I am after a business card that will fit the name of my business - velvette.
I want something classy and sexy and nothing tacky.
Ideas that I like are Zebra print backgrounds glitter back grounds
Two ideas I had were
1. Zebra print in black and white, the name Velvette by Marisa Dunn and a shilouette of a woman laying on top of the name. Or instead of zebra a glitter background.
2. Idea very similar except for instead of a woman a pair of lips maybe a hot pink glitter or a gold glitter depending on background with the business name between the lips.
Or you can do something completely different.

```html
<!DOCTYPE html>
<html lang="en">
<head>
<meta charset="utf-8">
<title>Velvette by Marisa Dunn — Business Card</title>
<link rel="stylesheet" href="https://fonts.googleapis.com/css2?family=Great+Vibes&family=Josefin+Sans:wght@100;300&display=swap">
<style>
  :root {
    --ink: #111111;
    --paper: #ffffff;
    --stripe-white: #f4f4f4;
    --stripe-light: #cfcfcf;
    --stripe-mid: #6e6e6e;
    --stripe-dark: #2e2e2e;
    --panel: rgba(214, 214, 214, 0.85);
    --silhouette: #121212;
  }
  html, body {
    margin: 0;
    padding: 0;
    width: 1200px;
    height: 686px;
    overflow: hidden;
    background: var(--paper);
  }
  .card {
    position: relative;
    width: 1200px;
    height: 686px;
    overflow: hidden;
    font-family: "Josefin Sans", sans-serif;
    color: var(--ink);
  }
  .card__pattern {
    position: absolute;
    inset: 0;
    background:
      radial-gradient(ellipse at 70% 75%, var(--stripe-mid) 0%, transparent 50%),
      linear-gradient(120deg, var(--stripe-dark) 0%, var(--stripe-white) 22%, var(--stripe-light) 45%, var(--stripe-mid) 72%, var(--stripe-dark) 100%);
  }
  .card__panel {
    position: absolute;
    left: 252px;
    top: 146px;
    width: 698px;
    height: 394px;
    border-radius: 18px;
    background: var(--panel);
  }
  .card__silhouette {
    position: absolute;
    left: 700px;
    top: 160px;
    width: 280px;
    height: 128px;
    border-radius: 45% 50% 20% 20%;
    background: var(--silhouette);
  }
  .brand {
    position: absolute;
    left: 262px;
    top: 300px;
    width: 680px;
    margin: 0;
    font-weight: 100;
    z-index: 1;
  }
  .brand__name {
    display: block;
    font-size: 122px;
    line-height: 1;
    letter-spacing: 0;
    text-transform: uppercase;
    text-align: center;
    text-shadow: 3px 6px 5px rgba(0, 0, 0, 0.25);
  }
  .brand__by {
    position: absolute;
    left: 388px;
    top: 140px;
    font-family: "Josefin Sans", sans-serif;
    font-weight: 300;
    font-size: 24px;
    line-height: 1;
    text-transform: uppercase;
    letter-spacing: 1px;
  }
  .brand__owner {
    position: absolute;
    left: 378px;
    top: 156px;
    font-family: "Great Vibes", cursive;
    font-weight: 400;
    font-size: 66px;
    line-height: 1;
    white-space: nowrap;
  }
</style>
</head>
<body>
  <main class="card">
    <div class="card__pattern" role="img" aria-label="Black and white zebra print background"></div>
    <div class="card__panel"></div>
    <div class="card__silhouette" role="img" aria-label="Silhouette of a woman reclining on top of the business name"></div>
    <h1 class="brand">
      <span class="brand__name">Velvette</span>
      <span class="brand__by">by</span>
      <span class="brand__owner">Marisa Dunn</span>
    </h1>
  </main>
</body>
</html>
```